Membership Based Medical Practice Website

We need a functioning website for a new Membership based medical practice. There will be an enrollment fee and a monthly fee. We would like to see designs that are modern, simple. Should use neutral light colors. Examples of sites we like are www.kellanmoorclinic.com and https://fernholtcare.com/ We also have a link that when "Join Now" is clicked it will go to the signup website.

Target Market(s)

Gay Men, local population, Age group 20 to 60's.

Industry/Entity Type

Medical

Coding

Coded - Design and coding required

Number of Pages Required

5+ page

Font styles to use
Sans Serif

Colors
ffffff
cee9f5
ecf7fb
cfeae6
edf8f6
aaaaaa
e9e9e9
dbdbdb
fff3d1

Requirements
Must have
• Logo and header on every page. Clean, simple design, clear content, mobile compatible.
• Must use Wordpress
Nice to have
• Ideas should come from kellanmoorclinic.com
• Easy to read
Should not have
• Generic patient pictures, bold colors.
• Should not copy from above websites.

```html
<!DOCTYPE html>
<html lang="en">
<head>
<meta charset="utf-8">
<title>Join Us – Larchfield Infectious Disease Specialists</title>
<link href="https://fonts.googleapis.com/css2?family=Lato:wght@300;400;700&display=swap" rel="stylesheet">
<style>
  :root {
    --white: #ffffff;
    --ink: #2f3338;
    --muted: #5b5f63;
    --band: #e6f4f9;
    --accent: #1a9ad6;
    --mint: #cfeae6;
    --cream: #fff3d1;
    --gold: #c9a45c;
    --road-dark: #3d4447;
    --field: #6b7a5c;
    --sky: #b9bec4;
  }
  * { box-sizing: border-box; margin: 0; padding: 0; }
  html, body { width: 1200px; height: 1163px; overflow: hidden; }
  body { font-family: "Lato", sans-serif; color: var(--ink); background: var(--white); position: relative; }

  .site-header { position: absolute; top: 0; left: 0; width: 1200px; height: 143px; }
  .brand { position: absolute; left: 74px; top: 14px; width: 184px; text-align: center; color: var(--muted); font-weight: 300; }
  .brand-mark { display: block; width: 64px; height: 64px; margin: 0 auto 12px; border: 1.5px solid var(--gold); border-radius: 50%; }
  .brand-name { display: block; font-size: 14px; letter-spacing: 14px; margin-right: -14px; line-height: 16px; }
  .brand-sub { display: block; font-size: 11.5px; letter-spacing: -0.2px; line-height: 16px; text-transform: uppercase; }

  .main-nav { position: absolute; right: 74px; top: 56px; display: flex; align-items: center; }
  .main-nav a { font-size: 14.5px; font-weight: 700; color: var(--ink); text-decoration: none; text-transform: uppercase; margin-left: 42px; }
  .main-nav a:first-child { margin-left: 0; }
  .main-nav .join-btn { margin-left: 26px; width: 120px; height: 42px; line-height: 42px; text-align: center; background: var(--mint); border-radius: 21px; font-size: 15.5px; letter-spacing: 0.5px; }

  .hero { position: absolute; top: 143px; left: 0; width: 1200px; height: 187px;
    background: linear-gradient(180deg, #9fa6ad 0%, var(--sky) 22%, #7f8a78 40%, var(--field) 62%, #55604a 100%); }
  .hero-road { position: absolute; inset: 0; background: linear-gradient(90deg, transparent 30%, rgba(45,50,54,.55) 45%, rgba(45,50,54,.75) 50%, rgba(45,50,54,.55) 58%, transparent 75%); }
  .hero-title { position: absolute; top: 76px; left: 0; width: 100%; text-align: center; font-size: 42px; font-weight: 700; color: var(--white); line-height: 1; }

  .content { position: absolute; top: 330px; left: 0; width: 1200px; height: 679px; background: var(--band); }
  .page-title { position: absolute; left: 74px; top: 63px; font-size: 33px; font-weight: 400; color: var(--muted); }
  .timeline-line { position: absolute; left: 103px; top: 185px; width: 3px; height: 240px; background: var(--accent); }
  .step-num { position: absolute; left: 75px; width: 59px; height: 59px; border-radius: 50%; background: var(--cream); border: 2.5px solid var(--accent);
    font-size: 28px; font-weight: 400; color: var(--ink); text-align: center; line-height: 54px; }
  .step-title { position: absolute; left: 150px; font-size: 19.5px; font-weight: 700; color: var(--accent); line-height: 59px; }
  .step-body { position: absolute; left: 151px; width: 990px; font-size: 14.5px; line-height: 29.5px; color: var(--ink); }
  .step-body p + p { margin-top: 12px; }
  .step-body a { color: var(--accent); text-decoration: none; }
  .step-body strong { font-weight: 700; }

  .site-footer { position: absolute; top: 1009px; left: 0; width: 1200px; height: 154px; text-align: center; }
  .footer-nav { margin-top: 31px; display: flex; justify-content: center; gap: 42px; }
  .footer-nav a { font-size: 14.5px; font-weight: 700; color: var(--ink); text-decoration: none; text-transform: uppercase; }
  .copyright { margin-top: 14px; font-size: 13.5px; color: var(--ink); }
  .social { margin-top: 14px; display: flex; justify-content: center; gap: 19px; }
  .social span { width: 20px; height: 20px; border-radius: 50%; background: #6f7377; display: block; }
</style>
</head>
<body>
  <header class="site-header">
    <div class="brand">
      <span class="brand-mark"></span>
      <span class="brand-name">LARCHFIELD</span>
      <span class="brand-sub">Infectious Disease Specialists</span>
    </div>
    <nav class="main-nav">
      <a href="#">Home</a>
      <a href="#">Specialties</a>
      <a href="#">Pricing</a>
      <a href="#">About Us</a>
      <a href="#">FAQ</a>
      <a href="#">Blog</a>
      <a href="#" class="join-btn">Join Us</a>
    </nav>
  </header>

  <section class="hero">
    <div class="hero-road" role="img" aria-label="Misty countryside road running through green fields"></div>
    <h1 class="hero-title">Join</h1>
  </section>

  <main class="content">
    <h2 class="page-title">Join Us</h2>
    <div class="timeline-line"></div>

    <div class="step-num" style="top:130px">1</div>
    <h3 class="step-title" style="top:130px">Call us to make an appointment</h3>

    <div class="step-num" style="top:218px">2</div>
    <h3 class="step-title" style="top:218px">Sign up with us</h3>
    <div class="step-body" style="top:274px">
      <p>Larchfield Infectious Disease Specialists has partnered with Tallyforth Health, a secure platform, to streamline our administrative processes.<br>
      The sign-up page will ask you for basic demographic information as well as a bank account or credit card number to keep on file. Tallyforth stores this information securely; Larchfield Infectious Disease Specialists does not have access to the numbers themselves. Your account will not be charged until your first visit.</p>
    </div>

    <div class="step-num" style="top:419px">3</div>
    <h3 class="step-title" style="top:419px">Check your email</h3>
    <div class="step-body" style="top:476px">
      <p>Once you have scheduled your appointment and signed up with the practice, Dr. Halloran will send you a welcome email with your new patient paperwork. Please fill them out and bring them with you to your appointment. If you are unable to complete them before your visit, please plan to arrive at least 15 minutes early.</p>
      <p>If you have any questions about our services before booking your appointment, please don't hesitate to email us at<br>
      <a href="#">info@larchfieldid.com</a> or c<strong>all us at 555-404-XXXX.</strong></p>
    </div>
  </main>

  <footer class="site-footer">
    <nav class="footer-nav">
      <a href="#">Home</a>
      <a href="#">Specialties</a>
      <a href="#">Pricing</a>
      <a href="#">About Us</a>
      <a href="#">FAQ</a>
      <a href="#">Blog</a>
    </nav>
    <p class="copyright">Copyright © 2019 CompanyName All Rights Reserved.</p>
    <div class="social" aria-label="Social links">
      <span></span><span></span><span></span><span></span><span></span>
    </div>
  </footer>
</body>
</html>
```